Band and Coaching business card (creative industry)

My company The Fenwick Ensemble is the name of my band Soul outfit but is also a brand I use for my coaching business which is Performance coaching in the following areas: Corporate coaching, acting, vocals and dialect. The band plays for corporate events and private functions as well as local bar/restaurant/festivals.
Updates

Hi All

Please see updated info for the wording of the business card front and back.  This is ito then be followed with contact number, email and facebook link

first side should have:

JulieRose Brannigan
Creative Director
( followed by contact info as per previous)

Side 2:

The Fenwick Ensemble  - Band  
 Vocalist      I   Musician    I  Songwriter

The Fenwick Ensemble  - Studio
Performance Coaching  
Acting  I  Vocals  I Dialect  I Corporate Coaching

Industry/Entity Type

Events

Contact Information for Business Card

The Fenwick Ensemble (logo)
JulieRose Brannigan
Musician/Vocalist/Performance Coach
M: 0412 605 918
E: thefenwickensemble@mailbrook.net
W: www.friendspace.net/thefenwickensembleband

Font styles to use
Sans Serif

Requirements
Must have
• first side should have:

JulieRose Brannigan
Creative Director

Side 2:

The Fenwick Ensemble - Band
Vocalist I Musician I Songwriter

The Fenwick Ensemble - Studio
Performance Coaching
Acting I Vocals I Dialect I Corporate Coaching
Nice to have
• I like smaller business cards with curved edges.

some ideas for look in additional business cards attached.
Should not have
• music notes or anything specific to the field. Want to keep it funky and contemporary

```html
<!DOCTYPE html>
<html lang="en">
<head>
<meta charset="utf-8">
<title>The Fenwick Ensemble – Band &amp; Studio</title>
<link rel="stylesheet" href="https://fonts.googleapis.com/css2?family=Open+Sans:wght@400;600&display=swap">
<style>
  :root {
    --paper: #ffffff;
    --brand-pink: #e2287f;
    --badge-fill: #b3308c;
    --badge-text: #ffffff;
  }
  html, body {
    margin: 0;
    padding: 0;
    width: 1200px;
    height: 602px;
    overflow: hidden;
    background: var(--paper);
  }
  .card {
    position: relative;
    width: 1200px;
    height: 602px;
    background: var(--paper);
    font-family: "Open Sans", Arial, sans-serif;
    color: var(--brand-pink);
  }
  .service {
    position: absolute;
    margin: 0;
    line-height: 1.2;
  }
  .service__title {
    display: block;
    font-size: 22px;
    font-weight: 600;
    white-space: nowrap;
  }
  .service__subtitle {
    display: block;
    font-size: 22px;
    font-weight: 600;
    white-space: nowrap;
  }
  .service__list {
    display: block;
    font-size: 17px;
    font-weight: 400;
    white-space: nowrap;
    margin-top: 2px;
  }
  .service--band {
    left: 42px;
    top: 270px;
  }
  .service--studio {
    left: 818px;
    top: 238px;
  }
  .badge {
    position: absolute;
    left: 400px;
    top: 147px;
    width: 390px;
    height: 390px;
  }
</style>
</head>
<body>
  <main class="card">
    <p class="service service--band">
      <span class="service__title">The Fenwick Ensemble - Band</span>
      <span class="service__list">Vocalist &nbsp;&nbsp; I &nbsp;Musician &nbsp; I &nbsp;Songwriter</span>
    </p>

    <svg class="badge" viewBox="0 0 390 390" role="img" aria-label="The Fenwick Ensemble">
      <circle cx="195" cy="195" r="195" fill="var(--badge-fill)"/>
      <text x="195" y="172" text-anchor="middle" fill="var(--badge-text)"
            font-family="Open Sans, Arial, sans-serif" font-weight="600" font-size="40">The Fenwick</text>
      <text x="195" y="228" text-anchor="middle" fill="var(--badge-text)"
            font-family="Open Sans, Arial, sans-serif" font-weight="600" font-size="40">Ensemble</text>
    </svg>

    <p class="service service--studio">
      <span class="service__title">The Fenwick Ensemble - Studio</span>
      <span class="service__subtitle">Performance Coaching</span>
      <span class="service__list">Acting I Vocals I Dialect I Corporate</span>
    </p>
  </main>
</body>
</html>
```